Corvel Capital LLC

Need Professional Business cards for New Investment Fund

Target Market(s)

High Quality investors

Industry/Entity Type

Financial

Contact Information for Business Card

Phone Number +1 555 284 6190
Name Lukas Varenko
Title Fund Manager
email lv@FundCorvel.com
Website www.FundCorvel.com

Colors

Designer to choose colors to be used in the design.

Requirements
Must have
• Must have our Logo and all of the above. Must be made so lettering and loge can be raised

```html
<!DOCTYPE html>
<html lang="en">
<head>
<meta charset="utf-8">
<title>Quenvar — Business Cards</title>
<link rel="stylesheet" href="https://fonts.googleapis.com/css2?family=Jost:wght@500&family=Roboto:wght@400;700&display=swap">
<style>
  :root {
    --backdrop: #bcbcbc;
    --forest: #3a4540;
    --paper: #f3f3f2;
    --ink: #3a4540;
    --ink-soft: #4f5753;
    --lime: #8cc63f;
    --mark-light: #c8ccc9;
  }
  * { margin: 0; padding: 0; box-sizing: border-box; }
  html, body { width: 1200px; height: 1138px; overflow: hidden; }
  body { background: var(--backdrop); position: relative; font-family: "Roboto", Arial, sans-serif; }

  .card {
    position: absolute;
    width: 622px;
    height: 374px;
    border-radius: 18px;
  }
  .card--front { left: 274px; top: 186px; background: var(--forest); }
  .card--back  { left: 276px; top: 608px; background: var(--paper); }

  .wordmark {
    position: absolute;
    display: flex;
    align-items: center;
    gap: 12px;
    font-family: "Jost", "Futura", sans-serif;
    font-weight: 500;
    letter-spacing: 1px;
    line-height: 1;
    white-space: nowrap;
  }
  .card--front .wordmark {
    left: 0; right: 0; top: 170px;
    justify-content: center;
    font-size: 62px;
    color: var(--mark-light);
  }
  .card--back .wordmark {
    right: 26px; top: 96px;
    font-size: 50px;
    color: var(--ink);
  }
  .wordmark__square { width: 26px; height: 26px; background: var(--lime); flex: none; }

  .holder { position: absolute; left: 26px; top: 264px; }
  .holder__name { font-size: 22px; font-weight: 700; color: var(--ink); line-height: 26px; }
  .holder__title { font-size: 14.5px; color: var(--ink-soft); line-height: 18px; margin-top: 1px; }

  .divider {
    position: absolute; left: 26px; right: 26px; top: 320px; height: 1.5px;
    background: linear-gradient(90deg, var(--lime) 0%, var(--lime) 30%, var(--ink) 60%);
  }

  .contacts {
    position: absolute; left: 26px; right: 26px; top: 331px;
    display: flex; justify-content: space-between; align-items: center;
    font-size: 15.5px; color: var(--ink-soft);
  }
  .contact { display: flex; align-items: center; gap: 9px; white-space: nowrap; }
  .contact svg { width: 15px; height: 15px; fill: var(--lime); flex: none; }
</style>
</head>
<body>

<section class="card card--front" aria-label="Card front">
  <div class="wordmark">QUENVAR</div>
</section>

<section class="card card--back" aria-label="Card back">
  <div class="wordmark"><span class="wordmark__square"></span>QUENVAR</div>

  <div class="holder">
    <div class="holder__name">Lukas Varenko</div>
    <div class="holder__title">Fund Manager</div>
  </div>

  <div class="divider"></div>

  <div class="contacts">
    <span class="contact">
      <svg viewBox="0 0 16 16"><path d="M2 6c0-2 2.5-3.5 6-3.5S14 4 14 6l-3 .5-.5-1.5h-5L5 6.5zM4 8h8l1.5 6h-11z"/></svg>
      +1 555 284 6190
    </span>
    <span class="contact">
      <svg viewBox="0 0 16 16"><path d="M1 3.5h14v9H1zM2 4.5l6 4.5 6-4.5" stroke="#f3f3f2" stroke-width="1.2"/></svg>
      lv@FundCorvel.com
    </span>
    <span class="contact">
      <svg viewBox="0 0 16 16"><circle cx="8" cy="8" r="7"/><path d="M1 8h14M8 1c-3 3.5-3 10.5 0 14M8 1c3 3.5 3 10.5 0 14" stroke="#f3f3f2" stroke-width="1" fill="none"/></svg>
      www.FundCorvel.com
    </span>
  </div>
</section>

</body>
</html>
```